Front page of Orthodox Christian Monastery Website

I am attaching a couple of versions of design that was already created for the front page of the website. You can grab the same pictures and titles (do not need to know the Russian language) to create your own version of design.
Background: Monastery website contains sermons, stories about monastery life, monastery music of the sisterhood.
Main principles of the design:
1. Various materials/sermons/music have to be clearly visible immediately to the site visitor.
2. Text descriptions to photos should be using font with a good contrast, highly clickable and easily readable.
3. Every article should have a photo or a quality picture (use those in the sample) that will convey something about it.
4. On the top, there will be a menu, which will be a line of words (just use generic words for now).
5. Design should reflect Christian Orthodox themes and fonts.
Updates

Target Market(s)

Orthodox Christian believers around the world and those that are interested in Orthodox Christianity

Number of Pages Required

1 page

Font styles to use
Serif

Colors

Designer to choose colors to be used in the design.

Requirements
Must have
• In the project description
Nice to have
• for some ideas see a popular Orthodox Christian website:
• www.verenskaya-lampada.ru
• We don't want to copy it, but it could give ideas.
Should not have
• Should not be overly complex

```html
<!DOCTYPE html>
<html lang="en">
<head>
<meta charset="utf-8">
<title>Orthodox Christian Monastery</title>
<link href="https://fonts.googleapis.com/css2?family=Montserrat:wght@400;600;700&family=Open+Sans:ital,wght@0,400;0,600;1,400&display=swap" rel="stylesheet">
<style>
:root{
  --green:#0f3d22;
  --green-dark:#0b2f1a;
  --search:#4a5a50;
  --ink:#111;
  --muted:#555;
  --page:#efefef;
  --white:#fff;
  --line:#e3e3e3;
  --footer:#ebebeb;
}
*{box-sizing:border-box;margin:0;padding:0}
html,body{width:1200px;height:3871px;overflow:hidden}
body{background:var(--page);font-family:"Open Sans",Arial,sans-serif;color:var(--ink);position:relative}
.abs{position:absolute}
.photo{position:absolute;display:block}
/* header */
.site-header{position:absolute;left:0;top:0;width:1200px;height:116px;background:var(--white)}
.brand{position:absolute;left:129px;top:26px;font-family:"Montserrat",sans-serif;color:var(--green);line-height:1.1}
.brand b{display:block;font-weight:700;font-size:27px}
.brand span{display:block;font-weight:400;font-size:27px}
.follow{position:absolute;left:702px;top:36px;font-size:14px;color:#333}
.follow-icons{position:absolute;left:702px;top:64px;display:flex;gap:12px}
.follow-icons i{width:14px;height:14px;border-radius:50%;background:#777;display:block}
.newsletter{position:absolute;left:880px;top:30px;font-size:13px;color:#333}
.newsletter-field{position:absolute;left:880px;top:57px;width:188px;height:26px;border:1px solid #bbb;font-size:11px;padding:5px 10px;color:#333}
.newsletter-field i{position:absolute;right:6px;top:6px;width:14px;height:12px;background:var(--green);border-radius:2px}
.main-nav{position:absolute;left:0;top:116px;width:1200px;height:34px;background:var(--green)}
.main-nav a{position:absolute;top:10px;font-family:"Montserrat",sans-serif;font-weight:700;font-size:11px;color:#fff;text-decoration:none}
.search{position:absolute;left:921px;top:0;width:147px;height:34px;background:var(--search);color:#cfd6d1;font-size:10px;font-family:"Montserrat",sans-serif;padding:11px 18px}
.search svg{position:absolute;right:14px;top:11px}
/* buttons */
.btn{display:inline-block;background:var(--green-dark);color:#fff;font-family:"Montserrat",sans-serif;font-weight:700;font-size:10px;padding:7px 12px;text-decoration:none}
/* hero */
.hero-tile{position:absolute;overflow:hidden}
.hero-cap{position:absolute;color:#fff}
.tag{display:inline-block;border:1px solid #fff;font-family:"Montserrat",sans-serif;font-weight:700;font-size:10px;padding:6px 9px}
.hero-title{font-family:"Montserrat",sans-serif;font-weight:700;font-size:19px}
.hero-text{font-size:12px}
/* sections */
.section-title{position:absolute;font-family:"Montserrat",sans-serif;font-weight:700;font-size:23px;color:var(--green)}
.view-all{position:absolute;width:80px;height:30px;background:var(--green-dark);color:#fff;font-family:"Montserrat",sans-serif;font-weight:700;font-size:10px;text-align:center;line-height:30px}
.card{position:absolute;background:var(--white);box-shadow:0 1px 4px rgba(0,0,0,.08)}
.item{position:absolute;left:0;width:100%;height:145px;border-bottom:1px solid var(--line)}
.item:last-child{border-bottom:none}
.item .photo{left:20px;top:24px;width:106px;height:98px}
.item .body{position:absolute;left:150px;top:22px;right:16px}
.date{font-style:italic;font-size:10px;color:#333}
.item h3{font-family:"Montserrat",sans-serif;font-weight:700;font-size:13px;line-height:1.25;margin-top:5px}
.item p{font-size:10px;color:var(--muted);line-height:1.35;margin-top:6px}
.more{display:block;font-family:"Montserrat",sans-serif;font-weight:700;font-size:9px;margin-top:9px}
.feature .photo{left:0;top:0;width:100%}
.feature .body{position:absolute;left:38px;right:38px}
.feature h3{font-family:"Montserrat",sans-serif;font-weight:700;font-size:15px;margin-top:8px}
.feature p{font-size:12px;color:var(--muted);line-height:1.4;margin-top:8px}
.feature .btn{margin-top:16px}
/* related */
.related{position:absolute;left:0;top:2915px;width:1200px;height:581px;background:var(--white)}
.arrows{position:absolute;left:1007px;top:90px;display:flex;gap:20px}
.rel-card{position:absolute;top:163px;width:273px}
.rel-card .photo{position:relative;width:273px;height:150px}
.rel-card h3{font-family:"Montserrat",sans-serif;font-weight:700;font-size:14px;line-height:1.25;margin-top:28px}
.rel-card p{font-size:11px;color:var(--muted);line-height:1.4;margin-top:12px;width:240px}
.rel-card .btn{margin-top:16px}
/* footer */
.site-footer{position:absolute;left:0;top:3496px;width:1200px;height:375px;background:var(--footer)}
.foot-h{position:absolute;font-family:"Montserrat",sans-serif;font-weight:700;font-size:11px}
.foot-list{position:absolute;font-size:11px;line-height:1.65;list-style:none;font-family:"Montserrat",sans-serif}
.social{position:absolute;display:flex;align-items:center;gap:10px;font-size:11px}
.social i{width:26px;height:26px;border-radius:50%;background:var(--green);display:block}
.copyright{position:absolute;left:0;width:1200px;top:3832px;text-align:center;font-size:11px;color:#333}
.foot-rule{position:absolute;left:529px;top:3793px;width:539px;height:1px;background:#cfcfcf}
</style>
</head>
<body>

<header class="site-header">
  <div class="brand"><b>Orthodox Christian</b><span>Monastery</span></div>
  <div class="follow">Follow us</div>
  <div class="follow-icons"><i></i><i></i><i></i><i></i><i></i></div>
  <div class="newsletter">Subscribe to our Newsletter</div>
  <div class="newsletter-field">E-mail id<i></i></div>
</header>
<nav class="main-nav">
  <a style="left:129px">HOME</a>
  <a style="left:222px">ABOUT US</a>
  <a style="left:341px">SERVICES</a>
  <a style="left:464px">ARTICLES</a>
  <a style="left:583px">NEWS</a>
  <a style="left:684px">CONTACT US</a>
  <div class="search">SEARCH
    <svg width="12" height="12" viewBox="0 0 12 12"><circle cx="5" cy="5" r="3.6" fill="none" stroke="#fff" stroke-width="1.6"/><line x1="7.6" y1="7.6" x2="11" y2="11" stroke="#fff" stroke-width="1.8"/></svg>
  </div>
</nav>

<!-- hero -->
<section class="hero-tile" style="left:132px;top:181px;width:627px;height:428px">
  <div class="photo" role="img" aria-label="Gothic cathedral interior with tall columns and vaulted ceiling" style="inset:0;background:linear-gradient(180deg,#6b5638 0%,#a08058 40%,#3a2c1d 100%)"></div>
  <div class="hero-cap" style="left:26px;top:316px">
    <span class="tag">HEADING 1</span>
    <div class="hero-title" style="margin-top:14px">Lorem Ipsum is simply dummy text of the print</div>
    <div class="hero-text" style="margin-top:4px">Lorem ipsum dolor sit amet, consectetur adipiscing elit.</div>
  </div>
  <a class="btn" style="position:absolute;left:521px;top:386px">READ MORE</a>
</section>
<section class="hero-tile" style="left:777px;top:181px;width:291px;height:257px">
  <div class="photo" role="img" aria-label="Choir singing in a church" style="inset:0;background:linear-gradient(180deg,#8a6a3a 0%,#4a3a22 60%,#1e1810 100%)"></div>
  <div class="hero-cap" style="left:14px;top:205px"><div style="font-family:Montserrat,sans-serif;font-weight:700;font-size:13px">Lorem Ipsum is simply</div><div style="font-size:11px">Lorem ipsum dolor sit</div></div>
  <a class="btn" style="position:absolute;left:201px;top:226px;font-size:9px;padding:6px 9px">READ MORE</a>
</section>
<section class="hero-tile" style="left:777px;top:452px;width:291px;height:157px">
  <div class="photo" role="img" aria-label="Orchestra performing in a hall" style="inset:0;background:linear-gradient(180deg,#6a3a26 0%,#3a2216 60%,#1a100a 100%)"></div>
  <div class="hero-cap" style="left:14px;top:110px"><div style="font-family:Montserrat,sans-serif;font-weight:700;font-size:13px">Lorem Ipsum</div><div style="font-size:11px">Lorem ipsum dolor</div></div>
  <a class="btn" style="position:absolute;left:201px;top:126px;font-size:9px;padding:6px 9px">READ MORE</a>
</section>

<!-- sermons -->
<h2 class="section-title" style="left:129px;top:701px">SERMONS</h2>
<div class="view-all" style="left:988px;top:701px">VIEW ALL</div>
<div class="card" style="left:132px;top:761px;width:402px;height:583px">
  <div class="item" style="top:0"><div class="photo" role="img" aria-label="Priest preaching at a pulpit" style="background:linear-gradient(#2a3a5a,#0e1420)"></div><div class="body"><div class="date">04 May,2018</div><h3>Lorem ipsum dolor sit amet cons ecetur adipiscing</h3><p>Sed ut perspiciatis unde omnis iste natus error sit voluptatem.</p><span class="more">READ MORE &rsaquo;</span></div></div>
  <div class="item" style="top:145px"><div class="photo" role="img" aria-label="Congregation listening in a church hall" style="background:linear-gradient(#5a4a6a,#2a1e30)"></div><div class="body"><div class="date">04 May,2018</div><h3>Lorem ipsum dolor sit amet cons ecetur adipiscing</h3><p>Sed ut perspiciatis unde omnis iste natus error sit voluptatem.</p><span class="more">READ MORE &rsaquo;</span></div></div>
  <div class="item" style="top:290px"><div class="photo" role="img" aria-label="Clergyman speaking at a lectern" style="background:linear-gradient(#9a8a9a,#5a3a4a)"></div><div class="body"><div class="date">04 May,2018</div><h3>Lorem ipsum dolor sit amet cons ecetur adipiscing</h3><p>Sed ut perspiciatis unde omnis iste natus error sit voluptatem.</p><span class="more">READ MORE &rsaquo;</span></div></div>
  <div class="item" style="top:435px"><div class="photo" role="img" aria-label="Sermon in a bright chapel" style="background:linear-gradient(#c8c0b0,#5a5040)"></div><div class="body"><div class="date">04 May,2018</div><h3>Lorem ipsum dolor sit amet cons ecetur adipiscing</h3><p>Sed ut perspiciatis unde omnis iste natus error sit voluptatem.</p><span class="more">READ MORE &rsaquo;</span></div></div>
</div>
<div class="card feature" style="left:552px;top:761px;width:516px;height:583px">
  <div class="photo" role="img" aria-label="Preacher reading scripture to a seated group" style="height:421px;background:linear-gradient(135deg,#7a6a5a 0%,#4a3a30 50%,#6a8a3a 100%)"></div>
  <div class="body" style="top:440px"><div class="date">04 May,2018</div><h3>Lorem ipsum dolor sit amet consectetur adipiscing</h3><p>Sed ut perspiciatis unde omnis iste natus error sit voluptatem accusantium doloremque laudantium, totam rem aperiam, eaque ipsa quae</p><a class="btn">READ MORE</a></div>
</div>

<!-- stories -->
<h2 class="section-title" style="left:129px;top:1443px">STORIES ABOUT MONASTERY LIFE</h2>
<div class="view-all" style="left:988px;top:1453px">VIEW ALL</div>
<div class="card feature" style="left:132px;top:1507px;width:516px;height:583px">
  <div class="photo" role="img" aria-label="Painted tile wall along a monastery walkway" style="height:421px;background:linear-gradient(135deg,#c8a050 0%,#8a6a3a 45%,#5a6a8a 100%)"></div>
  <div class="body" style="top:440px"><div class="date">04 May,2018</div><h3>Lorem ipsum dolor sit amet consectetur adipiscing</h3><p>Sed ut perspiciatis unde omnis iste natus error sit voluptatem accusantium doloremque laudantium, totam rem aperiam, eaque ipsa quae</p><a class="btn">READ MORE</a></div>
</div>
<div class="card" style="left:666px;top:1507px;width:402px;height:583px">
  <div class="item" style="top:0"><div class="photo" role="img" aria-label="Monastery building facade" style="background:linear-gradient(#9a7a5a,#4a3020)"></div><div class="body"><div class="date">04 May,2018</div><h3>Lorem ipsum dolor sit amet cons ecetur adipiscing</h3><p>Sed ut perspiciatis unde omnis iste natus error sit voluptatem.</p><span class="more">READ MORE &rsaquo;</span></div></div>
  <div class="item" style="top:145px"><div class="photo" role="img" aria-label="Carved stone archway" style="background:linear-gradient(#c08040,#5a3010)"></div><div class="body"><div class="date">04 May,2018</div><h3>Lorem ipsum dolor sit amet cons ecetur adipiscing</h3><p>Sed ut perspiciatis unde omnis iste natus error sit voluptatem.</p><span class="more">READ MORE &rsaquo;</span></div></div>
  <div class="item" style="top:290px"><div class="photo" role="img" aria-label="Monastery lit up at night" style="background:linear-gradient(#1a1e4a,#b08a30)"></div><div class="body"><div class="date">04 May,2018</div><h3>Lorem ipsum dolor sit amet cons ecetur adipiscing</h3><p>Sed ut perspiciatis unde omnis iste natus error sit voluptatem.</p><span class="more">READ MORE &rsaquo;</span></div></div>
  <div class="item" style="top:435px"><div class="photo" role="img" aria-label="Ornate painted church ceiling" style="background:linear-gradient(#d8c8a8,#8a6a4a)"></div><div class="body"><div class="date">04 May,2018</div><h3>Lorem ipsum dolor sit amet cons ecetur adipiscing</h3><p>Sed ut perspiciatis unde omnis iste natus error sit voluptatem.</p><span class="more">READ MORE &rsaquo;</span></div></div>
</div>

<!-- music -->
<h2 class="section-title" style="left:129px;top:2180px">MONASTERY MUSIC OF THE SISTERHOOD</h2>
<div class="view-all" style="left:988px;top:2190px">VIEW ALL</div>
<div class="card" style="left:132px;top:2238px;width:402px;height:583px">
  <div class="item" style="top:0"><div class="photo" role="img" aria-label="Nun singing" style="background:linear-gradient(#6a5a40,#1a1410)"></div><div class="body"><div class="date">04 May,2018</div><h3>Lorem ipsum dolor sit amet cons ecetur adipiscing</h3><p>Sed ut perspiciatis unde omnis iste natus error sit voluptatem.</p><span class="more">READ MORE &rsaquo;</span></div></div>
  <div class="item" style="top:145px"><div class="photo" role="img" aria-label="Sisters in black habits" style="background:linear-gradient(#d0d0d0,#141414)"></div><div class="body"><div class="date">04 May,2018</div><h3>Lorem ipsum dolor sit amet cons ecetur adipiscing</h3><p>Sed ut perspiciatis unde omnis iste natus error sit voluptatem.</p><span class="more">READ MORE &rsaquo;</span></div></div>
  <div class="item" style="top:290px"><div class="photo" role="img" aria-label="Sisterhood choir performing" style="background:linear-gradient(#8a5a3a,#2a1a14)"></div><div class="body"><div class="date">04 May,2018</div><h3>Lorem ipsum dolor sit amet cons ecetur adipiscing</h3><p>Sed ut perspiciatis unde omnis iste natus error sit voluptatem.</p><span class="more">READ MORE &rsaquo;</span></div></div>
  <div class="item" style="top:435px"><div class="photo" role="img" aria-label="Nuns reading music sheets" style="background:linear-gradient(#b0a090,#2a2220)"></div><div class="body"><div class="date">04 May,2018</div><h3>Lorem ipsum dolor sit amet cons ecetur adipiscing</h3><p>Sed ut perspiciatis unde omnis iste natus error sit voluptatem.</p><span class="more">READ MORE &rsaquo;</span></div></div>
</div>
<div class="card feature" style="left:552px;top:2238px;width:516px;height:583px">
  <div class="photo" role="img" aria-label="Nun singing on a stage under blue light" style="height:421px;background:linear-gradient(180deg,#1a2a8a 0%,#0a1240 60%,#04061a 100%)"></div>
  <div class="body" style="top:440px"><div class="date">04 May,2018</div><h3>Lorem ipsum dolor sit amet consectetur adipiscing</h3><p>Sed ut perspiciatis unde omnis iste natus error sit voluptatem accusantium doloremque laudantium, totam rem aperiam, eaque ipsa quae</p><a class="btn">READ MORE</a></div>
</div>

<!-- related -->
<section class="related">
  <h2 class="section-title" style="left:132px;top:80px">RELATED ARTICLES</h2>
  <div class="arrows">
    <svg width="12" height="18" viewBox="0 0 12 18"><path d="M10 2 3 9l7 7" fill="none" stroke="#999" stroke-width="2.4"/></svg>
    <svg width="12" height="18" viewBox="0 0 12 18"><path d="M2 2l7 7-7 7" fill="none" stroke="#777" stroke-width="2.4"/></svg>
  </div>
  <article class="rel-card" style="left:132px"><div class="photo" role="img" aria-label="Ancient stone ruins among trees" style="background:linear-gradient(#8aa0b8,#5a5a4a)"></div><h3>At vero eos et accusamus<br>et iusto odio.</h3><p>On the other hand, we denounce with righteous indignation and dislike men who are so beguiled</p><a class="btn">READ MORE</a></article>
  <article class="rel-card" style="left:452px"><div class="photo" role="img" aria-label="Vaulted cloister corridor" style="background:linear-gradient(#c8c0b0,#5a5044)"></div><h3>At vero eos et accusamus<br>et iusto odio.</h3><p>On the other hand, we denounce with righteous indignation and dislike men who are so beguiled</p><a class="btn">READ MORE</a></article>
  <article class="rel-card" style="left:777px"><div class="photo" role="img" aria-label="Temple facade carved in red rock" style="background:linear-gradient(#d08a4a,#6a3a1a)"></div><h3>At vero eos et accusamus<br>et iusto odio.</h3><p>On the other hand, we denounce with righteous indignation and dislike men who are so beguiled</p><a class="btn">READ MORE</a></article>
</section>

<!-- footer -->
<footer class="site-footer">
  <div class="brand" style="left:142px;top:106px"><b>Orthodox Christian</b><span>Monastery</span></div>
  <div class="foot-h" style="left:529px;top:78px">CONTACT US</div>
  <div class="abs" style="left:529px;top:110px;font-size:11px;line-height:1.5;display:flex;gap:14px">
    <svg width="10" height="14" viewBox="0 0 10 14"><path d="M5 0a5 5 0 0 0-5 5c0 4 5 9 5 9s5-5 5-9a5 5 0 0 0-5-5z" fill="#333"/><circle cx="5" cy="5" r="1.8" fill="#ebebeb"/></svg>
    <div>17 Cloister Lane<br>Hillford, IL 60999</div>
  </div>
  <div class="abs" style="left:529px;top:162px;font-size:11px;display:flex;gap:14px;align-items:center">
    <svg width="11" height="11" viewBox="0 0 11 11"><path d="M2 0l2 3-1.2 1.3a6 6 0 0 0 3.9 3.9L8 7l3 2-1 2C5 11 0 6 0 1z" fill="#333"/></svg>
    <span>555.010.0100</span>
  </div>
  <div class="foot-h" style="left:784px;top:78px">MENU</div>
  <ul class="foot-list" style="left:784px;top:105px"><li>HOME</li><li>ABOUT US</li><li>SERVICES</li><li>ARTICLES</li><li>NEWS</li><li>CONTACT US</li></ul>
  <div class="foot-h" style="left:955px;top:78px">CONNECT WITH US</div>
  <div class="social" style="left:955px;top:110px"><i></i>Gathering</div>
  <div class="social" style="left:955px;top:150px"><i></i>Chirp</div>
  <div class="social" style="left:955px;top:190px"><i></i>Network</div>
</footer>
<div class="foot-rule"></div>
<div class="copyright">Copyrights @ 2018 All Rights Reserved</div>

</body>
</html>
```